Custom hot rod builder needs a website for launch of new business where he will build luxury garages

We need a website that gives a WOW first impression for "Summit Carports". This is a new business so photos are renderings but we need it to really attract a particular audience. Our initial business is custom hot rods so now we are building garages for them. These will be like luxury "homes" for cars! I will attach our new logo. Website needs to feel powerful and prestigious.

Target Market(s)

middle aged men, car enthusiasts

Industry/Entity Type

automotive, construction

Coding

Coded - Design and coding required

Number of Pages Required

2 page

Font styles to use
Serif

Colors
0054AA
0677BA
7BADD7
CADEEF
E8F1F8

Requirements
Must have
• a WOW factor. luxury. contact form.
Nice to have
• ?

```html
<!DOCTYPE html>
<html lang="en">
<head>
<meta charset="utf-8">
<title>Summit Carports</title>
<link rel="stylesheet" href="https://fonts.googleapis.com/css2?family=Orbitron:wght@800;900&family=Roboto:wght@700&family=Mulish:wght@400;600;700&display=swap">
<style>
:root{
  --blue-deep:#0054AA;
  --blue:#0677BA;
  --blue-mid:#7BADD7;
  --blue-pale:#CADEEF;
  --blue-mist:#E8F1F8;
  --cyan:#1EB4E6;
  --ink:#1c1c1c;
  --text:#333;
  --night:#1f2228;
  --white:#fff;
}
*{margin:0;padding:0;box-sizing:border-box}
html,body{width:1200px;height:3536px;overflow:hidden}
body{position:relative;font-family:"Mulish",sans-serif;color:var(--text);background:var(--white)}
.abs{position:absolute}
.display{font-family:"Orbitron",sans-serif;font-weight:900;letter-spacing:2px;color:var(--ink)}
.btn{position:absolute;display:flex;align-items:center;justify-content:center;font-size:11px;font-weight:700;letter-spacing:1px;text-transform:uppercase}
.btn-white{background:var(--white);color:var(--ink)}
.btn-blue{background:var(--blue);color:var(--white)}
.photo{position:absolute}

/* hero */
.hero{position:absolute;left:0;top:0;width:1200px;height:533px;background:linear-gradient(180deg,#2b3036 0%,#1d2126 55%,#2c2f33 100%)}
.hero-glow{position:absolute;left:640px;top:90px;width:420px;height:380px;background:radial-gradient(circle at 50% 50%,#5d6570 0%,#3a4048 45%,rgba(40,44,50,0) 75%)}
.topbar{position:absolute;left:130px;top:0;width:940px;height:24px;display:flex;align-items:center;color:var(--white);font-size:11px}
.topbar .social{display:flex;gap:16px}
.topbar .social span{width:8px;height:8px;background:var(--white);border-radius:50%}
.topbar .contact{margin-left:auto;display:flex;gap:38px}
.topbar .contact span{display:flex;align-items:center;gap:6px}
.nav{position:absolute;left:130px;top:26px;width:940px;height:50px;background:var(--white);display:flex;align-items:center;padding:0 12px}
.brand{display:flex;align-items:center;gap:8px;font-weight:700;font-size:19px;color:var(--blue)}
.brand i{width:26px;height:26px;border-radius:50%;background:var(--blue)}
.nav ul{margin-left:auto;display:flex;list-style:none;gap:50px;font-size:12px;color:var(--ink)}
.nav ul li:first-child{color:var(--blue)}
.hero-kicker{left:131px;top:150px;font-size:38px;color:var(--cyan)}
.hero-title{position:absolute;left:131px;top:203px;font-family:"Roboto",sans-serif;font-weight:700;font-size:34px;line-height:36px;color:var(--white)}
.hero-lede{position:absolute;left:131px;top:286px;width:460px;font-size:14px;line-height:18px;color:var(--white)}

/* welcome */
.welcome-kicker{position:absolute;left:130px;top:650px;font-size:17px;color:var(--blue)}
.welcome-title{left:130px;top:678px;font-size:33px}
.welcome-body{position:absolute;left:130px;top:743px;width:465px;font-size:12.5px;line-height:20px;color:var(--ink)}

/* services */
.band{position:absolute;left:0;width:1200px}
.services-kicker{position:absolute;left:0;width:1200px;top:1102px;text-align:center;font-size:17px;color:var(--white)}
.services-title{left:0;width:1200px;top:1128px;text-align:center;font-size:33px;color:var(--white)}
.card-title{position:absolute;width:300px;text-align:center;font-size:16px;font-weight:600;color:var(--white)}
.card-text{position:absolute;width:300px;text-align:center;font-size:11.5px;line-height:16px;color:var(--blue-mist)}

/* why */
.why-title{left:510px;top:1758px;font-size:33px}
.feature{position:absolute;width:300px;height:70px}
.feature h3{position:absolute;left:80px;top:0;font-size:16px;font-weight:600;color:var(--ink)}
.feature p{position:absolute;left:80px;top:26px;width:205px;font-size:11.5px;line-height:17px;color:#555}
.feature svg{position:absolute;left:0;top:-2px}

/* contact */
.contact-kicker{position:absolute;left:0;width:1200px;top:2132px;text-align:center;font-size:17px;color:var(--white)}
.contact-title{left:0;width:1200px;top:2157px;text-align:center;font-size:33px;color:var(--white)}
.contact-sub{position:absolute;left:0;width:1200px;top:2204px;text-align:center;font-size:13px;color:var(--white)}
.field{position:absolute;background:var(--white);font-size:10px;color:#333;padding:11px 10px}
.submit{position:absolute;left:611px;top:2335px;width:249px;height:35px;background:var(--blue-deep);color:var(--white);font-size:11px;display:flex;align-items:center;justify-content:center}

/* gallery */
.gallery-title{left:0;width:1200px;top:2624px;text-align:center;font-size:33px}

/* footer */
.footer-brand{position:absolute;left:130px;top:3290px}
.footer-brand .brand{color:var(--white)}
.footer-brand .brand i{background:var(--white)}
.footer-about{position:absolute;left:130px;top:3352px;width:265px;font-size:11.5px;line-height:17px;color:var(--white)}
.footer-social{position:absolute;left:130px;top:3419px;display:flex;gap:14px}
.footer-social span{width:34px;height:34px;border:1.5px solid var(--white);border-radius:50%}
.col{position:absolute;top:3280px;color:var(--white)}
.col h4{font-size:14px;font-weight:600;margin-bottom:16px}
.col li{list-style:none;font-size:11.5px;line-height:26.5px}
.col-contact li{display:flex;align-items:center;gap:10px;margin-bottom:22px;line-height:14px}
.col-contact li i{flex:none;width:28px;height:28px;border-radius:50%;background:var(--blue)}
.copyright{position:absolute;left:0;width:1200px;top:3500px;text-align:center;font-size:10px;color:var(--white)}
</style>
</head>
<body>

<!-- Hero -->
<section class="hero" role="img" aria-label="Evening rendering of a modern luxury garage building with glass walls and parked classic cars"></section>
<div class="hero-glow"></div>
<div class="topbar">
  <div class="social"><span></span><span></span><span></span></div>
  <div class="contact">
    <span><svg width="12" height="9" viewBox="0 0 12 9"><rect x="0.5" y="0.5" width="11" height="8" fill="none" stroke="#fff"/><path d="M0.5 0.5 6 5 11.5 0.5" fill="none" stroke="#fff"/></svg>hello@summitcarports.com</span>
    <span><svg width="11" height="11" viewBox="0 0 24 24"><path fill="#fff" d="M6.6 10.8a15 15 0 0 0 6.6 6.6l2.2-2.2c.3-.3.7-.4 1-.2 1.1.4 2.3.6 3.6.6.6 0 1 .4 1 1V20c0 .6-.4 1-1 1A17 17 0 0 1 3 4c0-.6.4-1 1-1h3.5c.6 0 1 .4 1 1 0 1.3.2 2.5.6 3.6.1.3 0 .7-.2 1z"/></svg>+1 (555) 014 2290</span>
  </div>
</div>
<nav class="nav">
  <div class="brand"><i></i>Summit Carports</div>
  <ul><li>Home</li><li>About Us</li><li>Services</li><li>Gallery</li><li>Contact Us</li></ul>
</nav>
<div class="abs display hero-kicker">SUMMIT</div>
<h1 class="hero-title">WE ARCHITECT YOUR<br>GARAGED</h1>
<p class="hero-lede">If you use this site regularly and would like to help keep the site on the Internet...</p>
<div class="btn btn-white" style="left:132px;top:339px;width:114px;height:33px">Get Started</div>

<!-- Welcome -->
<div class="welcome-kicker">Welcome To</div>
<h2 class="abs display welcome-title">SUMMIT CARPORTS</h2>
<p class="welcome-body">But I must explain to you how all this mistaken idea of denouncing pleasure and praising pain was born and I will give you a complete account of the system, and expound the actual teachings of the great explorer of the truth, the master-builder of human happiness. No one rejects, dislikes, or avoids pleasure itself, because it is pleasure.</p>
<div class="btn btn-blue" style="left:130px;top:868px;width:116px;height:33px">Read More</div>
<div class="photo" role="img" aria-label="Interior of a wood-panelled showroom garage with classic cars under track lights" style="left:611px;top:600px;width:460px;height:356px;background:linear-gradient(160deg,#6b3f1f 0%,#a8672c 40%,#3d4a44 75%,#8a2a22 100%)"></div>

<!-- Services -->
<svg class="band" style="top:1023px" width="1200" height="677" viewBox="0 0 1200 677" aria-hidden="true">
  <defs><linearGradient id="svcGrad" x1="0" y1="0" x2="1" y2="1"><stop offset="0" stop-color="#0a4f8c"/><stop offset="1" stop-color="#0668b0"/></linearGradient></defs>
  <polygon points="0,0 371,0 600,55 824,0 1200,0 1200,677 824,677 600,625 371,677 0,677" fill="url(#svcGrad)"/>
</svg>
<div class="services-kicker">Expertise</div>
<h2 class="abs display services-title">OUR SERVICES</h2>

<div class="photo" role="img" aria-label="Silver SUV charging beside a timber-clad garage door" style="left:130px;top:1188px;width:300px;height:291px;border-radius:8px;background:linear-gradient(180deg,#8aa07a 0%,#b08656 45%,#9aa0a6 75%,#6f8a4a 100%)"></div>
<div class="photo" role="img" aria-label="Silver SUV parked inside a bright garage with grey cabinets" style="left:450px;top:1188px;width:300px;height:291px;border-radius:8px;background:linear-gradient(180deg,#4b4e55 0%,#c9ccd0 40%,#a9adb2 70%,#8e9197 100%)"></div>
<div class="photo" role="img" aria-label="White electric car charging in front of a modern two-storey house" style="left:770px;top:1188px;width:300px;height:291px;border-radius:8px;background:linear-gradient(180deg,#7fb0dd 0%,#cfd6d8 45%,#d8d8d4 70%,#9a9c98 100%)"></div>

<div class="card-title" style="left:130px;top:1498px">Nostrum Exercitationem</div>
<div class="card-title" style="left:450px;top:1498px">Nostrum Exercitationem</div>
<div class="card-title" style="left:770px;top:1498px">Nostrum Exercitationem</div>
<p class="card-text" style="left:130px;top:1533px">Sed ut perspiciatis unde omnis iste natus error sit voluptatem accusantium doloremque</p>
<p class="card-text" style="left:450px;top:1533px">Sed ut perspiciatis unde omnis iste natus error sit voluptatem accusantium doloremque</p>
<p class="card-text" style="left:770px;top:1533px">Sed ut perspiciatis unde omnis iste natus error sit voluptatem accusantium doloremque</p>
<div class="btn btn-white" style="left:223px;top:1583px;width:114px;height:33px">Read More</div>
<div class="btn btn-white" style="left:543px;top:1583px;width:114px;height:33px">Read More</div>
<div class="btn btn-white" style="left:863px;top:1583px;width:114px;height:33px">Read More</div>

<!-- Why choose us -->
<div class="photo" role="img" aria-label="Suburban house with solar roof, double garage and two cars in the driveway" style="left:130px;top:1767px;width:337px;height:266px;background:linear-gradient(170deg,#5f7f4a 0%,#d9d4c8 35%,#c08a52 65%,#7d9a5a 100%)"></div>
<h2 class="abs display why-title">WHY CHOOSE US</h2>

<div class="feature" style="left:508px;top:1852px">
  <svg width="62" height="66" viewBox="0 0 62 66"><path d="M4 26a28 28 0 0 1 54 0" fill="none" stroke="#1EB4E6" stroke-width="3"/><path d="M58 40a28 28 0 0 1-54 0" fill="none" stroke="#0677BA" stroke-width="3"/><path d="M20 33 31 24 42 33M23 31v12h16V31M28 43v-6h6v6" fill="none" stroke="#0677BA" stroke-width="2"/></svg>
  <h3>Quia Moluptas</h3><p>Sed ut perspiciatis unde omnis iste natus error sit voluptatem</p>
</div>
<div class="feature" style="left:805px;top:1852px">
  <svg width="62" height="66" viewBox="0 0 62 66"><path d="M4 26a28 28 0 0 1 54 0" fill="none" stroke="#1EB4E6" stroke-width="3"/><path d="M58 40a28 28 0 0 1-54 0" fill="none" stroke="#0677BA" stroke-width="3"/><path d="M21 29 31 22 41 29M23 29v15h16V29M23 33h16M23 37h16M23 41h16" fill="none" stroke="#0677BA" stroke-width="2"/></svg>
  <h3>Quia Moluptas</h3><p>Sed ut perspiciatis unde omnis iste natus error sit voluptatem</p>
</div>
<div class="feature" style="left:508px;top:1973px">
  <svg width="62" height="66" viewBox="0 0 62 66"><path d="M4 26a28 28 0 0 1 54 0" fill="none" stroke="#1EB4E6" stroke-width="3"/><path d="M58 40a28 28 0 0 1-54 0" fill="none" stroke="#0677BA" stroke-width="3"/><path d="M22 36l3-8h12l3 8v6H22zM22 36h18" fill="none" stroke="#0677BA" stroke-width="2"/><circle cx="26" cy="39" r="1.5" fill="#0677BA"/><circle cx="36" cy="39" r="1.5" fill="#0677BA"/></svg>
  <h3>Quia Moluptas</h3><p>Sed ut perspiciatis unde omnis iste natus error sit voluptatem</p>
</div>
<div class="feature" style="left:805px;top:1973px">
  <svg width="62" height="66" viewBox="0 0 62 66"><path d="M4 26a28 28 0 0 1 54 0" fill="none" stroke="#1EB4E6" stroke-width="3"/><path d="M58 40a28 28 0 0 1-54 0" fill="none" stroke="#0677BA" stroke-width="3"/><circle cx="31" cy="33" r="8" fill="none" stroke="#0677BA" stroke-width="2"/><circle cx="31" cy="33" r="3" fill="#0677BA"/><path d="M31 22v3M31 41v3M20 33h3M39 33h3" stroke="#0677BA" stroke-width="2"/></svg>
  <h3>Quia Moluptas</h3><p>Sed ut perspiciatis unde omnis iste natus error sit voluptatem</p>
</div>

<!-- Contact -->
<svg class="band" style="top:2101px" width="1200" height="462" viewBox="0 0 1200 462" role="img" aria-label="Blue-tinted night view of a modern garage building">
  <defs><linearGradient id="ctGrad" x1="0" y1="0" x2="0" y2="1"><stop offset="0" stop-color="#163a63"/><stop offset="1" stop-color="#0d4a8a"/></linearGradient></defs>
  <polygon points="0,0 1200,0 1200,302 669,462 0,123" fill="url(#ctGrad)"/>
</svg>
<div class="contact-kicker">Contact Us</div>
<h2 class="abs display contact-title">GET IN TOUCH</h2>
<p class="contact-sub">But I must explain to you how all this mistaken idea of denouncing</p>
<div class="field" style="left:350px;top:2242px;width:249px;height:33px">Name:</div>
<div class="field" style="left:350px;top:2289px;width:249px;height:34px">Email:</div>
<div class="field" style="left:350px;top:2335px;width:249px;height:35px">Phone:</div>
<div class="field" style="left:611px;top:2242px;width:249px;height:81px">Message:</div>
<div class="submit">SUBMIT</div>

<!-- Gallery -->
<h2 class="abs display gallery-title">GALLERY</h2>
<div class="photo" role="img" aria-label="Garage building exterior with palm trees" style="left:130px;top:2684px;width:220px;height:158px;background:linear-gradient(180deg,#a9c3dc 0%,#d7d9d6 55%,#8f918e 100%)"></div>
<div class="photo" role="img" aria-label="Showroom garage interior with classic cars" style="left:369px;top:2684px;width:221px;height:158px;background:linear-gradient(160deg,#6b3f1f 0%,#a8672c 45%,#3d4a44 100%)"></div>
<div class="photo" role="img" aria-label="Garage building frontage at daytime" style="left:610px;top:2684px;width:221px;height:158px;background:linear-gradient(180deg,#b2c9de 0%,#d1d3cf 55%,#8c8e8b 100%)"></div>
<div class="photo" role="img" aria-label="Bright white workshop with car lifts" style="left:850px;top:2684px;width:220px;height:158px;background:linear-gradient(180deg,#f2f3f4 0%,#dfe2e5 60%,#b9bec4 100%)"></div>
<div class="photo" role="img" aria-label="Modern white house with lit garage at dusk" style="left:130px;top:2863px;width:220px;height:158px;background:linear-gradient(180deg,#5b6470 0%,#cfcfcd 50%,#4c5a3f 100%)"></div>
<div class="photo" role="img" aria-label="Contemporary house with open garage and solar roof" style="left:369px;top:2863px;width:221px;height:158px;background:linear-gradient(180deg,#dfe6ec 0%,#8a7458 45%,#5c7a3e 100%)"></div>
<div class="photo" role="img" aria-label="Dark sports car beside red storage cabinets" style="left:610px;top:2863px;width:221px;height:158px;background:linear-gradient(160deg,#e9e9e9 0%,#b3202a 45%,#1b1b1d 100%)"></div>
<div class="photo" role="img" aria-label="White villa with a car on the driveway" style="left:850px;top:2863px;width:220px;height:158px;background:linear-gradient(180deg,#e3e7ea 0%,#cfd1cf 50%,#7d9a4e 100%)"></div>

<!-- Footer -->
<svg class="band" style="top:3070px" width="1200" height="466" viewBox="0 0 1200 466" aria-hidden="true">
  <g stroke="#9aa5b1" stroke-width="1" fill="none">
    <line x1="47" y1="110" x2="200" y2="190"/>
    <line x1="105" y1="95" x2="600" y2="130"/>
    <line x1="510" y1="30" x2="1190" y2="230"/>
    <line x1="655" y1="50" x2="960" y2="150"/>
  </g>
  <circle cx="512" cy="30" r="4" fill="#0054AA"/>
  <circle cx="107" cy="95" r="4" fill="#0054AA"/>
  <circle cx="655" cy="50" r="4" fill="#0054AA"/>
  <polygon points="688,20 695,24 695,32 688,36 681,32 681,24" fill="none" stroke="#0677BA" stroke-width="2"/>
  <circle cx="688" cy="28" r="3" fill="#0677BA"/>
  <polygon points="0,225 529,60 1200,239 1200,466 0,466" fill="#0054AA"/>
</svg>
<div class="footer-brand"><div class="brand"><i></i>Summit Carports</div></div>
<p class="footer-about">Sed ut perspiciatis unde omnis iste natus error sit voluptatem accusantium doloremque laudantium, totam rem aperiam...</p>
<div class="footer-social"><span></span><span></span><span></span></div>
<div class="col" style="left:450px"><h4>Quick Links</h4><ul><li>Home</li><li>About Us</li><li>Services</li><li>Gallery</li><li>Contact Us</li></ul></div>
<div class="col" style="left:642px"><h4>Services</h4><ul><li>Molestiae Consequatur</li><li>Exercitationem Ullam</li><li>Avoids Pleasure</li><li>Minima Aspernatur</li></ul></div>
<div class="col col-contact" style="left:859px"><h4>Contact Us</h4><ul>
  <li><i></i>42 Ridgeway Lane Stonebrook<br>10KL USA</li>
  <li><i></i>+1 (555) 014 2290</li>
  <li><i></i>hello@summitcarports.com</li>
</ul></div>
<p class="copyright">Copyright © 2022 Summit Carports. All Rights Reserved.</p>

</body>
</html>
```